Business Card & Email Signature Design || Upmarket + Luxury

Rima Vale Honey, a New Zealand Manuka Honey company needs a Business Card & Email Signature design.

Our logo's are attached in Gold & Black versions, feel free to be creative with how you use the logo and it's patterns in your design.

Style:
- Looking for an Elegant, Luxurious, Upmarket feel.
- Black/Matte Black Card, Gold Foil, UV Embossing

Information to Add:

- Logo
- Company Name: Rima Vale Honey
- Name: Martin Holloway
- Title: Creative Director
- Phone: +64 2815 96 417
- Email: martin@rimavalehoney.example.nz
- Website: www.rimavalehoney.example.nz

- Socials: ***For email Signature Only***
- Facebook: https://www.facebook.com/rimavalehoney/
- Instagram: https://www.instagram.com/rimavalehoney/

Target Market(s)

Asia/Europe Luxury, Upmarket

Contact Information for Business Card

- Logo
- Name: Martin Holloway
- Phone: +64 2815 96 417

Font styles to use
Other font styles liked:
• Champagne & Limousines (Attached)

Requirements
Must have
• Business Card & Email Signature Design.

Looking for a Sleek, Luxury, Upmarket Design.

```html
<!DOCTYPE html>
<html lang="en">
<head>
<meta charset="utf-8">
<title>Rima Vale Honey — Business Card</title>
<link href="https://fonts.googleapis.com/css2?family=Josefin+Sans:wght@300;400&family=Questrial&display=swap" rel="stylesheet">
<style>
  :root {
    --backdrop: #1b1b1b;
    --card: #121314;
    --card-edge: #0c0d0e;
    --comb-light: #3a3b3d;
    --comb-dark: #151617;
    --gold: #c9a95c;
    --gold-light: #ecd896;
    --gold-deep: #a3843a;
    --ink: #e6e6e6;
  }
  * { box-sizing: border-box; margin: 0; padding: 0; }
  html, body { width: 1200px; height: 675px; overflow: hidden; background: var(--backdrop); }
  .stage { position: relative; width: 1200px; height: 675px; }

  .card {
    position: absolute; top: 195px; width: 500px; height: 286px;
    background: var(--card); overflow: hidden;
    box-shadow: 0 18px 40px rgba(0,0,0,.55);
  }
  .card--front { left: 60px; }
  .card--back { left: 640px; }

  .comb-texture {
    position: absolute; inset: 0;
    background: radial-gradient(ellipse at 35% 10%, var(--comb-light) 0%, var(--comb-dark) 55%, var(--card) 80%);
    opacity: .75;
  }

  /* Front */
  .brand { position: absolute; inset: 0; display: flex; flex-direction: column; align-items: center; }
  .brand__mark {
    width: 70px; height: 70px; margin-top: 32px; border-radius: 50%;
    border: 1.5px solid var(--gold);
  }
  .brand__name {
    margin-top: 48px; font-family: "Josefin Sans", sans-serif; font-weight: 300;
    font-size: 29px; letter-spacing: 4px; color: var(--gold); white-space: nowrap;
  }
  .brand__web {
    margin-top: 18px; font-family: "Questrial", sans-serif; font-size: 13px;
    letter-spacing: .3px; color: var(--ink);
  }

  /* Back */
  .gold-band {
    position: absolute; left: 38px; width: 18px;
    background: linear-gradient(90deg, var(--gold-deep), var(--gold-light) 50%, var(--gold-deep));
  }
  .gold-band--top { top: 0; height: 196px; }
  .gold-band--bottom { top: 256px; height: 30px; }

  .contact { position: absolute; left: 68px; top: 120px; font-family: "Questrial", sans-serif; }
  .contact__title {
    font-family: "Josefin Sans", sans-serif; font-weight: 300; font-size: 12px; color: var(--ink);
    display: inline-block; border-bottom: 1px solid var(--ink); padding-bottom: 1px;
  }
  .contact__name { margin-top: 4px; font-size: 25px; color: var(--ink); letter-spacing: .5px; white-space: nowrap; }
  .contact__list { list-style: none; margin-top: 16px; margin-left: -42px; }
  .contact__item { display: flex; align-items: center; gap: 18px; font-size: 11.5px; color: var(--ink); height: 18px; margin-bottom: 6px; }
  .contact__item svg { width: 14px; height: 14px; flex: none; }
  .contact__label { color: #cfcfcf; margin-right: 4px; }

  .seal {
    position: absolute; right: 36px; top: 120px; width: 84px;
    display: flex; flex-direction: column; align-items: center; gap: 8px;
  }
  .seal__ring { width: 54px; height: 54px; border-radius: 50%; border: 1.2px solid var(--gold); }
  .seal__name {
    font-family: "Josefin Sans", sans-serif; font-weight: 300; font-size: 8px;
    letter-spacing: 1.2px; color: var(--gold); text-align: center; white-space: nowrap;
  }
</style>
</head>
<body>
<main class="stage">

  <section class="card card--front" aria-label="Business card front">
    <div class="comb-texture" role="img" aria-label="Honeycomb pattern in dark grey"></div>
    <div class="brand">
      <div class="brand__mark"></div>
      <p class="brand__name">RIMA VALE HONEY CO.</p>
      <p class="brand__web">www.rimavalehoney.example.nz</p>
    </div>
  </section>

  <section class="card card--back" aria-label="Business card back">
    <div class="comb-texture" role="img" aria-label="Honeycomb pattern in dark grey"></div>
    <div class="gold-band gold-band--top"></div>
    <div class="gold-band gold-band--bottom"></div>

    <div class="contact">
      <p class="contact__title">Creative Director</p>
      <h1 class="contact__name">MARTIN HOLLOWAY</h1>
      <ul class="contact__list">
        <li class="contact__item">
          <svg viewBox="0 0 24 24" aria-hidden="true"><path fill="#c9a95c" d="M6.6 10.8c1.4 2.8 3.8 5.1 6.6 6.6l2.2-2.2c.3-.3.7-.4 1-.2 1.1.4 2.3.6 3.6.6.6 0 1 .4 1 1V20c0 .6-.4 1-1 1C10.6 21 3 13.4 3 4c0-.6.4-1 1-1h3.5c.6 0 1 .4 1 1 0 1.3.2 2.5.6 3.6.1.3 0 .7-.2 1z"/></svg>
          <span><span class="contact__label">Phone:</span>+64 2815 96 417</span>
        </li>
        <li class="contact__item">
          <svg viewBox="0 0 24 24" aria-hidden="true"><rect x="3" y="5.5" width="18" height="13" fill="none" stroke="#c9a95c" stroke-width="1.8"/><path d="M3 6l9 7 9-7" fill="none" stroke="#c9a95c" stroke-width="1.8"/></svg>
          <span><span class="contact__label">Email:</span>martin@rimavalehoney.example.nz</span>
        </li>
      </ul>
    </div>

    <div class="seal">
      <div class="seal__ring"></div>
      <p class="seal__name">RIMA VALE HONEY CO.</p>
    </div>
  </section>

</main>
</body>
</html>
```